Bramwell Corner Sports Pub. Where the locals go!!

We are creating a sports pub. We are needing a fun website that offers our menu along with an event page and general info. We have some attached links that we really like:
https://www.dunmorrows.example/
https://www.cafepelindra.example/
https://www.quillstoneyx.example/
We are doing a pirate theme but that is because the area we are in. We would like to see a pirate like in our logo doing something like drinking real time similar to the dunmorrows website above.
Target Market(s)
Sports Fans
Industry/Entity Type
Pub, Bar, Restaurant
Coding
Coded - Design and coding required
Number of Pages Required
3 page
Font styles to use
Other font styles liked:
- see uploads
Look and feel

```html
<!DOCTYPE html>
<html lang="en">
<head>
<meta charset="utf-8">
<title>Bramwell Corner Sports Pub</title>
<link href="https://fonts.googleapis.com/css2?family=Bebas+Neue&family=Special+Elite&display=swap" rel="stylesheet">
<style>
:root{
  --parchment:#c8b498;
  --parchment-light:#d6c6ad;
  --parchment-dark:#a8967c;
  --ink:#2a2521;
  --card:#333231;
  --card-shadow:#111;
  --cream:#efe6d6;
  --tan:#c9a386;
  --footer:#1c1b1a;
}
*{box-sizing:border-box;margin:0;padding:0}
html,body{width:1200px;height:3860px;overflow:hidden}
body{position:relative;font-family:"Special Elite",monospace;color:var(--ink);
  background:radial-gradient(ellipse at 30% 40%,var(--parchment-light),var(--parchment) 55%,var(--parchment-dark));}
.display{font-family:"Bebas Neue",sans-serif;letter-spacing:1px}
.abs{position:absolute}
.btn{position:absolute;display:flex;align-items:center;justify-content:center;background:var(--card);color:var(--cream);
  font-family:"Bebas Neue",sans-serif;font-size:21px;letter-spacing:1px;box-shadow:-5px 5px 0 var(--card-shadow)}

/* header */
.site-header{position:absolute;left:0;top:0;width:1200px;height:118px;background:var(--parchment-light)}
.contact-label{position:absolute;font-family:"Bebas Neue",sans-serif;font-size:14px;line-height:15px;color:var(--ink)}
.contact-label span{display:block;color:#6d6257;font-size:15px}
.nav a{position:absolute;top:72px;font-family:"Bebas Neue",sans-serif;font-size:19px;color:#6d6257;text-decoration:none;letter-spacing:.5px}
.nav a.current{color:var(--ink)}
.brand-badge{position:absolute;left:488px;top:-44px;width:224px;height:224px;border-radius:50%;background:#dccaa9;
  display:flex;align-items:flex-end;justify-content:center;padding-bottom:40px;text-align:center}
.brand-badge p{font-family:"Bebas Neue",sans-serif;font-size:28px;line-height:28px;color:var(--ink);width:150px}

/* hero */
.hero{position:absolute;left:0;top:118px;width:1200px;height:672px}
.hero-frame{position:absolute;left:258px;top:307px;width:687px;height:243px;border:4px solid rgba(235,225,210,.35)}
.hero h1{position:absolute;left:0;width:1200px;top:322px;text-align:center;font-family:"Bebas Neue",sans-serif;font-size:76px;color:var(--cream);font-weight:400}
.hero .lead{position:absolute;left:320px;width:560px;top:404px;text-align:center;font-size:19px;line-height:29px;color:var(--cream)}
.dots{position:absolute;left:576px;top:662px;display:flex;gap:6px}
.dots i{width:8px;height:8px;border-radius:50%;background:#bbb}
.dots i.on{background:none;border:2px solid #ddd}

/* about */
.about-photo{position:absolute;left:116px;top:872px;width:460px;height:460px;border-radius:50%;border:18px solid #3a3836;
  background:radial-gradient(circle at 50% 30%,#b8402c,#6a2a1c 45%,#2c1b14 80%)}
.section-title{position:absolute;font-family:"Bebas Neue",sans-serif;font-size:58px;color:var(--ink);text-shadow:2px 2px 0 rgba(0,0,0,.25)}
.rule{position:absolute;height:4px;background:var(--ink)}
.about-text{position:absolute;left:626px;top:975px;width:475px;font-size:15.5px;line-height:24.7px;color:#3b342e}

/* menus */
.menu-card{position:absolute;width:297px;height:199px;background:var(--card);color:var(--cream);text-align:center;box-shadow:-7px 7px 0 var(--card-shadow);padding:14px 10px 0}
.menu-card h3{font-family:"Bebas Neue",sans-serif;font-weight:400;font-size:22px;letter-spacing:.5px}
.menu-card p{font-size:10.5px;line-height:14.5px;margin-top:9px}
.menu-card hr{width:66px;margin:12px auto 6px;border:0;border-top:2px solid var(--cream)}
.menu-card .was{font-family:"Bebas Neue",sans-serif;font-size:19px;color:#9a948c;text-decoration:line-through}
.menu-card .now{font-family:"Bebas Neue",sans-serif;font-size:34px;line-height:32px}

/* gallery */
.shot{position:absolute;border:14px solid #111;box-shadow:0 4px 10px rgba(0,0,0,.4)}

/* footer */
.site-footer{position:absolute;left:0;top:3405px;width:1200px;height:455px}
.footer-brand{position:absolute;left:90px;top:3680px;width:195px;text-align:center;font-family:"Bebas Neue",sans-serif;font-size:38px;line-height:36px;color:var(--cream)}
.footer-col h4{position:absolute;top:3512px;font-family:"Bebas Neue",sans-serif;font-weight:400;font-size:22px;color:var(--parchment)}
.footer-col ul{position:absolute;top:3552px;list-style:none;font-size:11px;line-height:20.5px;color:var(--cream);text-transform:uppercase}
.field{position:absolute;background:#000;border:1px solid #333;color:#bbb;font-size:12px;padding:11px 12px}
.submit{position:absolute;left:639px;top:3747px;width:116px;height:34px;background:var(--tan);color:var(--ink);
  font-family:"Bebas Neue",sans-serif;font-size:17px;display:flex;align-items:center;justify-content:center}
.copyright{position:absolute;left:0;width:1200px;top:3833px;text-align:center;font-size:10px;color:var(--cream)}
</style>
</head>
<body>

<header class="site-header">
  <div class="contact-label" style="left:110px;top:18px">Email<span>hello@bramwellcornerpub.example</span></div>
  <div class="contact-label" style="left:802px;top:18px">Call us now<span>+1 555 014 2290</span></div>
  <div class="btn" style="left:940px;top:9px;width:146px;height:40px">Contact Us</div>
  <nav class="nav">
    <a class="current" style="left:110px">Home</a>
    <a style="left:176px">Hours &amp; Location</a>
    <a style="left:324px">About</a>
    <a style="left:396px">Press</a>
    <a style="left:802px">Menus</a>
    <a style="left:876px">Private Events</a>
    <a style="left:1008px">Gift Cards</a>
  </nav>
</header>

<section class="hero">
  <svg class="abs" style="left:0;top:0" width="1200" height="672" viewBox="0 0 1200 672">
    <defs>
      <linearGradient id="heroFill" x1="0" y1="0" x2="0" y2="1">
        <stop offset="0" stop-color="#3a2418"/>
        <stop offset=".45" stop-color="#6b3a22"/>
        <stop offset="1" stop-color="#2a1810"/>
      </linearGradient>
    </defs>
    <path role="img" aria-label="Pub interior photo with wooden tables and screens"
      fill="url(#heroFill)" d="M0 0H1200V640L1170 648 1130 632 1090 650 1040 638 990 660 940 644 900 662 850 646 800 668 760 652 700 664 650 650 600 668 560 655 500 664 450 648 400 660 350 645 300 662 250 650 200 666 150 652 100 660 60 646 20 658 0 650Z"/>
  </svg>
  <div class="hero-frame" style="top:189px"></div>
  <h1 style="top:204px">Bramwell Corner Sports Pub</h1>
  <p class="lead" style="top:286px">Saers lkses sepiciatis unde omnis iste natus error sit voluptatem asccusan tium doloremque.</p>
  <div class="btn" style="left:530px;top:362px;width:143px;height:40px">Contact Us</div>
  <div class="dots" style="top:544px"><i></i><i class="on"></i><i></i><i></i></div>
</section>

<div class="brand-badge"><p>Bramwell Corner</p></div>

<section class="about">
  <div class="about-photo" role="img" aria-label="Crowd of guests at the pub bar"></div>
  <h2 class="section-title" style="left:627px;top:878px">About Us</h2>
  <div class="rule" style="left:627px;top:948px;width:93px"></div>
  <p class="about-text">Saerspiciatis undeasepoiise osamnis istasesee njhhjkatus error ssaeeacit voluptatem accusan tiaseum doloreasmque laudantium, totam resem aperiam, ease aque ipaefdsa quae abasllo inventore veritatis ease quasi architecto beatae vitae diascta ssadceunt explicabo. Nesemo enimsae ipsam voluptatem quia voaslupta sdasdse sessitasese aspernatur autodit aut asdsadfug tsdsed quia conseq aauuntur magni dolores eosasdqui ratione voluptatem sequi nesciunt.</p>
  <div class="btn" style="left:630px;top:1203px;width:143px;height:40px">Contact Us</div>
</section>

<section class="menus">
  <h2 class="section-title" style="left:0;width:1200px;text-align:center;top:1452px">Menus</h2>
  <div class="rule" style="left:555px;top:1516px;width:90px"></div>

  <div class="menu-card" style="left:123px;top:1563px"><h3>Consectetur adipiscin</h3><p>Saerspiciatis undeasepoiise osamnis istasesee njhhjkatus error ssaeeacit voluptatem accusan tiaseum doloreasmque laudantium, totam resem aperiam</p><hr><div class="was">$ 50.00</div><div class="now">$ 40.00</div></div>
  <div class="menu-card" style="left:457px;top:1563px"><h3>Consectetur adipiscin</h3><p>Saerspiciatis undeasepoiise osamnis istasesee njhhjkatus error ssaeeacit voluptatem accusan tiaseum doloreasmque laudantium, totam resem aperiam</p><hr><div class="was">$ 50.00</div><div class="now">$ 40.00</div></div>
  <div class="menu-card" style="left:790px;top:1563px"><h3>Consectetur adipiscin</h3><p>Saerspiciatis undeasepoiise osamnis istasesee njhhjkatus error ssaeeacit voluptatem accusan tiaseum doloreasmque laudantium, totam resem aperiam</p><hr><div class="was">$ 50.00</div><div class="now">$ 40.00</div></div>

  <div class="menu-card" style="left:123px;top:1803px"><h3>Consectetur adipiscin</h3><p>Saerspiciatis undeasepoiise osamnis istasesee njhhjkatus error ssaeeacit voluptatem accusan tiaseum doloreasmque laudantium, totam resem aperiam</p><hr><div class="was">$ 50.00</div><div class="now">$ 40.00</div></div>
  <div class="menu-card" style="left:457px;top:1803px"><h3>Consectetur adipiscin</h3><p>Saerspiciatis undeasepoiise osamnis istasesee njhhjkatus error ssaeeacit voluptatem accusan tiaseum doloreasmque laudantium, totam resem aperiam</p><hr><div class="was">$ 50.00</div><div class="now">$ 40.00</div></div>
  <div class="menu-card" style="left:790px;top:1803px"><h3>Consectetur adipiscin</h3><p>Saerspiciatis undeasepoiise osamnis istasesee njhhjkatus error ssaeeacit voluptatem accusan tiaseum doloreasmque laudantium, totam resem aperiam</p><hr><div class="was">$ 50.00</div><div class="now">$ 40.00</div></div>

  <div class="menu-card" style="left:123px;top:2041px"><h3>Consectetur adipiscin</h3><p>Saerspiciatis undeasepoiise osamnis istasesee njhhjkatus error ssaeeacit voluptatem accusan tiaseum doloreasmque laudantium, totam resem aperiam</p><hr><div class="was">$ 50.00</div><div class="now">$ 40.00</div></div>
  <div class="menu-card" style="left:457px;top:2041px"><h3>Consectetur adipiscin</h3><p>Saerspiciatis undeasepoiise osamnis istasesee njhhjkatus error ssaeeacit voluptatem accusan tiaseum doloreasmque laudantium, totam resem aperiam</p><hr><div class="was">$ 50.00</div><div class="now">$ 40.00</div></div>
  <div class="menu-card" style="left:790px;top:2041px"><h3>Consectetur adipiscin</h3><p>Saerspiciatis undeasepoiise osamnis istasesee njhhjkatus error ssaeeacit voluptatem accusan tiaseum doloreasmque laudantium, totam resem aperiam</p><hr><div class="was">$ 50.00</div><div class="now">$ 40.00</div></div>

  <div class="btn" style="left:528px;top:2285px;width:146px;height:40px">View All</div>
</section>

<section class="gallery">
  <h2 class="section-title" style="left:0;width:1200px;text-align:center;top:2436px">Gallery</h2>
  <div class="rule" style="left:555px;top:2500px;width:90px"></div>

  <div class="shot" role="img" aria-label="Long wooden bar counter with beer taps" style="left:155px;top:2575px;width:450px;height:318px;transform:rotate(-10deg);background:linear-gradient(160deg,#5a3a22,#b0702f 50%,#2a1a10)"></div>
  <div class="shot" role="img" aria-label="Colourful bar walls covered in sports memorabilia" style="left:640px;top:2585px;width:455px;height:320px;transform:rotate(10deg);background:linear-gradient(150deg,#4a5a8a,#b06040 50%,#3a2a24)"></div>
  <div class="shot" role="img" aria-label="Warm string lights over a dim pub interior" style="left:125px;top:2925px;width:460px;height:318px;transform:rotate(3deg);background:radial-gradient(ellipse at 50% 35%,#c8783a,#5a2e16 60%,#1e120c)"></div>
  <div class="shot" role="img" aria-label="Leather booth seating under framed sports jerseys" style="left:600px;top:2925px;width:465px;height:318px;transform:rotate(-6deg);background:linear-gradient(180deg,#3a2e2a,#6a3a26 60%,#241814)"></div>

  <div class="btn" style="left:530px;top:3311px;width:146px;height:42px">View All</div>
</section>

<footer class="site-footer">
  <svg class="abs" style="left:0;top:0" width="1200" height="455" viewBox="0 0 1200 455">
    <path fill="#1c1b1a" d="M0 40L20 28 60 44 100 30 150 46 190 34 240 50 300 38 360 52 420 40 480 54 540 42 600 56 660 44 720 56 780 42 840 54 900 40 960 52 1020 38 1080 50 1140 34 1200 46V455H0Z"/>
  </svg>
</footer>
<div class="footer-brand">Bramwell Corner</div>

<div class="footer-col">
  <h4 style="left:350px">Quick Links</h4>
  <ul style="left:350px"><li>Home</li><li>Hours &amp; Location</li><li>About</li><li>Press</li><li>Menus</li><li>Private Events</li><li>Gift Cards</li><li>Contact Us</li></ul>
  <h4 style="left:503px">Links</h4>
  <ul style="left:503px"><li>Copyright</li><li>Legal</li><li>Privacy</li><li>Accessibility</li><li>Sitemap</li></ul>
  <h4 style="left:637px">Contact Us</h4>
</div>
<div class="field" style="left:637px;top:3549px;width:218px;height:38px">Name</div>
<div class="field" style="left:876px;top:3549px;width:219px;height:38px">Phone</div>
<div class="field" style="left:637px;top:3605px;width:458px;height:130px">Enter Your Message</div>
<div class="submit">Submit</div>
<div class="abs" style="left:110px;top:3808px;width:980px;height:1px;background:#555"></div>
<p class="copyright">©2023. ALL RIGHTS RESERVED.</p>

</body>
</html>
```